Birchpoint Studio Complementary Pass

I’d like a complimentary pass for any 30-minute Birchpoint Studio session. Choose one of the following options: Infrared Sauna with Red Light, Massage Chair Veltrafix Compression Therapy, or Paraffin Wax Hand Bath.

Please incorporate the logo and brand colors into your design. I’d like a square image that will be printed on square business cards (no rectangles).

Please refer to the logo and menu for more details.

Contact Information for Business Card

See discretion

```html
<!DOCTYPE html>
<html lang="en">
<head>
<meta charset="utf-8">
<title>Birchpoint Studio Complimentary Pass</title>
<link rel="stylesheet" href="https://fonts.googleapis.com/css2?family=Kaushan+Script&family=Montserrat:wght@600;800&family=Roboto:wght@400;500&display=swap">
<style>
  :root {
    --orange: #f0694a;
    --purple: #4a2f92;
    --ink-purple: #3f2a86;
    --white: #ffffff;
    --backdrop: #2a2a2a;
  }
  * { box-sizing: border-box; margin: 0; padding: 0; }
  html, body { width: 1200px; height: 800px; overflow: hidden; }
  body {
    background: var(--backdrop);
    font-family: "Roboto", Arial, sans-serif;
    position: relative;
  }
  .card {
    position: absolute;
    top: 150px;
    width: 500px;
    height: 500px;
    border-radius: 34px;
    overflow: hidden;
  }
  /* Front side */
  .card-front {
    left: 70px;
    background: linear-gradient(160deg, var(--orange) 0%, #a24b79 50%, var(--purple) 100%);
    display: flex;
    align-items: center;
    justify-content: center;
    gap: 16px;
  }
  .brand-dot {
    width: 34px; height: 34px; border-radius: 50%;
    background: var(--white);
    flex-shrink: 0;
  }
  .brand-name {
    font-family: "Montserrat", Arial, sans-serif;
    font-weight: 600;
    color: var(--white);
    font-size: 44px;
    line-height: 1.05;
  }
  /* Back side */
  .card-back {
    left: 630px;
    background: var(--white);
  }
  .back-wave { position: absolute; inset: 0; }
  .back-brand {
    position: absolute; top: 36px; left: 0; right: 0;
    display: flex; justify-content: center; align-items: center; gap: 10px;
  }
  .back-brand .brand-dot { width: 18px; height: 18px; background: var(--orange); }
  .back-brand .brand-name { font-size: 24px; color: var(--purple); }
  .title-row {
    position: absolute; top: 108px; left: 40px; right: 40px;
    display: flex; align-items: center; gap: 14px;
  }
  .title-row .rule { flex: 1; height: 2px; background: var(--purple); }
  .title-script {
    font-family: "Kaushan Script", cursive;
    color: var(--purple);
    font-size: 34px;
    white-space: nowrap;
  }
  .pass-title {
    position: absolute; top: 168px; left: 0; right: 0;
    text-align: center;
    font-family: "Montserrat", Arial, sans-serif;
    font-weight: 800;
    color: var(--orange);
    font-size: 31px;
    letter-spacing: 0.5px;
  }
  .pass-offer {
    position: absolute; top: 212px; left: 0; right: 0;
    text-align: center;
    color: var(--ink-purple);
    font-size: 17px;
    line-height: 1.45;
  }
  .pass-offer .accent { color: var(--orange); }
  .pass-offer .choose { color: var(--orange); font-family: "Montserrat", Arial, sans-serif; font-weight: 800; }
  .option {
    position: absolute;
    color: var(--white);
    font-size: 14px;
    line-height: 1.25;
    text-align: center;
    border-radius: 8px;
    padding: 8px 10px;
    display: flex; align-items: center; justify-content: center;
    height: 52px;
  }
  .option-sauna { left: 26px; top: 330px; width: 128px; background: var(--orange); }
  .option-massage { left: 162px; top: 306px; width: 176px; background: var(--purple); }
  .option-wax { left: 346px; top: 282px; width: 128px; background: var(--orange); }
  .contact {
    position: absolute; left: 44px; top: 410px;
    list-style: none;
    color: var(--white);
    font-size: 11.5px;
    line-height: 1.3;
  }
  .contact li { display: flex; align-items: flex-start; gap: 8px; margin-bottom: 4px; }
  .contact svg { width: 12px; height: 12px; flex-shrink: 0; margin-top: 1px; }
  .safety-note {
    position: absolute; right: 30px; top: 404px; width: 210px;
    color: var(--white);
    font-size: 10.5px;
    line-height: 1.35;
    text-align: right;
  }
</style>
</head>
<body>
  <section class="card card-front" aria-label="Pass front">
    <span class="brand-dot"></span>
    <div class="brand-name">Lumora<br>Physical Therapy</div>
  </section>

  <section class="card card-back" aria-label="Pass back">
    <svg class="back-wave" viewBox="0 0 500 500" preserveAspectRatio="none" aria-hidden="true">
      <path d="M0 470 C40 400 120 385 240 372 C380 356 470 330 500 262 L500 500 L0 500 Z" fill="#4a2f92"/>
      <path d="M0 500 L0 482 C50 410 130 398 245 386 C385 370 478 348 500 292 L500 500 Z" fill="#f0694a"/>
    </svg>

    <div class="back-brand">
      <span class="brand-dot"></span>
      <span class="brand-name">Lumora Physical Therapy</span>
    </div>

    <div class="title-row">
      <span class="rule"></span>
      <span class="title-script">Birchpoint Studio</span>
      <span class="rule"></span>
    </div>

    <h1 class="pass-title">COMPLIMENTARY PASS</h1>
    <p class="pass-offer">Any <span class="accent">30-Minute</span> Birchpoint Studio Session.<br>on us! <span class="choose">Choose one:</span></p>

    <div class="option option-sauna">Infrared Sauna<br>+ Red Light</div>
    <div class="option option-massage">Massage Chair Veltrafix<br>Compression Therapy</div>
    <div class="option option-wax">Paraffin Wax<br>Hand Bath</div>

    <ul class="contact">
      <li>
        <svg viewBox="0 0 12 12"><path d="M6 1a3.5 3.5 0 0 0-3.5 3.5C2.5 7 6 11 6 11s3.5-4 3.5-6.5A3.5 3.5 0 0 0 6 1zm0 4.8a1.3 1.3 0 1 1 0-2.6 1.3 1.3 0 0 1 0 2.6z" fill="#fff"/></svg>
        <span>Street, Apartment, City, State,<br>Post Code, Country</span>
      </li>
      <li>
        <svg viewBox="0 0 12 12"><path d="M3 1l2 2.5-1.2 1.2a6 6 0 0 0 3.5 3.5L8.5 7 11 9l-1.3 1.6C6 11 1 6 1.4 2.3z" fill="#fff"/></svg>
        <span>(555) 014-2290</span>
      </li>
      <li>
        <svg viewBox="0 0 12 12"><circle cx="6" cy="6" r="4.8" fill="none" stroke="#fff" stroke-width="1.2"/><path d="M1.2 6h9.6M6 1.2c-2 2.6-2 7 0 9.6M6 1.2c2 2.6 2 7 0 9.6" fill="none" stroke="#fff" stroke-width="1"/></svg>
        <span>www.lumorapt.com</span>
      </li>
      <li>
        <svg viewBox="0 0 12 12"><rect x="1" y="2.5" width="10" height="7" rx="1" fill="none" stroke="#fff" stroke-width="1.2"/><path d="M1.5 3l4.5 3.5L10.5 3" fill="none" stroke="#fff" stroke-width="1.2"/></svg>
        <span>hello@lumorapt.com</span>
      </li>
    </ul>

    <p class="safety-note">*For safety, a rest/cool-down period is required after 30 minutes in the sauna.</p>
  </section>
</body>
</html>
```